Website for Scientific & Engineering Organization

Overview

The objective is to design a professional, easy-to-navigate, and visually appealing website for the <Enclosed Organization (see attached files)>, reflecting their esteemed status in the engineering and scientific community.

Pages:

Home (About Us) : Introduce the organization, highlighting their activities, history, and fellowship. Include a section for latest news highlights.

News and Programme : Dedicated page for news updates and detailed annual programmes

Gallery : This page will feature photographs and descriptions of the society's 'Voyages' and events.

Downloads : A section offering downloadable content such as newsletters and lecture materials, organized for user-friendliness.

Members Section : A private area for members to access exclusive content. Alternatively, a 'Membership' page with joining details and benefits if more public-facing content is preferred.

Design Elements:

Layout : A linear layout with a fixed top navigation bar for easy movement between pages.
Color Scheme : Utilize the provided colors (#395394, #E00053, #0043E1) to create a cohesive and professional aesthetic.
Typography : Use a combination of serif for headings and sans-serif for body text, ensuring readability and elegance.

Features:

Responsive Design : The design will accommodate various devices, ensuring consistency across mobiles, tablets, and desktops.

Accessibility : Design for all users with adequate spacing around elements and color contrasts

Content Strategy (Visual Focus):

Home Page : Visual emphasis on the introduction, mission, and recent 'Voyages' with engaging imagery and concise text.
News and Programme : Clear, visually distinct sections for news and the annual schedule
Gallery : A visually rich page with a grid or album layout, allowing users to easily browse through the years and events.
Downloads : Neatly organized sections with clear labels and icons to represent the different types of available downloads. Downloads are PDF newsletter/flyers/programmes etc...
Members Section/Membership : A design that conveys exclusivity and value, encouraging sign-ups and engagement from members.
Design Considerations:

Consistency : Ensure the design reflects the organization's heritage and professionalism throughout all pages.
User Experience : Focus on intuitive navigation and information architecture to guide visitors smoothly through the site.
Visual Hierarchy : Use size, color, and layout to emphasize key areas and direct user attention effectively.
Final Notes:

This design spec focuses on creating a web presence that mirrors the organization's prestige and heritage, providing an engaging, informative platform for members and the public alike. The design will be crafted to allow for easy content updates and adaptability, ensuring a long-lasting and effective website.

Target Market(s)

Non profit science and engineering. Older people

Industry/Entity Type

Non profit scientific organization

Number of Pages Required

5+ page

Requirements
Should not have
• No search feature

```html
<!DOCTYPE html>
<html lang="en">
<head>
<meta charset="utf-8">
<title>FSEA British Section</title>
<link href="https://fonts.googleapis.com/css2?family=Montserrat:wght@400;500;600;700;800&display=swap" rel="stylesheet">
<style>
:root{
  --navy:#395394;
  --crimson:#e00053;
  --red:#c8102e;
  --ink:#111111;
  --text:#333333;
  --muted:#555555;
  --white:#ffffff;
  --line:#e6e6e6;
  --black:#000000;
}
*{box-sizing:border-box;margin:0;padding:0}
html,body{width:1200px;height:4441px;overflow:hidden}
body{font-family:'Montserrat',sans-serif;color:var(--text);background:var(--white);position:relative}
a{color:inherit;text-decoration:none}

/* header */
.site-header{position:absolute;top:0;left:0;width:1200px;height:107px;background:var(--white);border-top:3px solid var(--crimson)}
.brand{position:absolute;left:105px;top:20px;display:flex;align-items:center;gap:10px}
.brand-dot{width:16px;height:16px;border-radius:50%;background:var(--crimson)}
.brand-name{font-weight:800;font-size:34px;color:var(--navy);letter-spacing:1px}
.brand-sub{position:absolute;left:105px;top:68px;font-size:8px;color:var(--navy);letter-spacing:.5px;font-weight:500}
.main-nav{position:absolute;left:385px;top:46px;display:flex;gap:24px;font-size:14px;color:#333}

/* hero */
.hero{position:absolute;top:107px;left:0;width:1200px;height:630px;overflow:hidden}
.hero-photo{position:absolute;inset:0;
  background:
    radial-gradient(ellipse 260px 420px at 1000px 380px,rgba(230,130,40,.9),rgba(230,130,40,0) 70%),
    radial-gradient(ellipse 500px 260px at 420px 80px,rgba(255,190,110,.75),rgba(255,190,110,0) 70%),
    linear-gradient(180deg,#d58a3d 0%,#9a5a2a 45%,#4a3224 100%)}
.hero-shade{position:absolute;inset:0;background:linear-gradient(90deg,rgba(40,25,15,.55) 0%,rgba(40,25,15,.15) 55%,rgba(0,0,0,0) 100%)}
.hero-brand{position:absolute;left:105px;top:92px;display:flex;align-items:center;gap:14px}
.hero-brand .mark{width:22px;height:22px;border-radius:50%;background:var(--white)}
.hero-brand .name{font-size:66px;font-weight:800;color:var(--white);letter-spacing:2px}
.hero-tag{position:absolute;left:105px;top:190px;font-size:12px;color:var(--white);font-weight:500;letter-spacing:.5px}
.hero-title{position:absolute;left:105px;top:240px;color:var(--white);font-weight:800;text-transform:uppercase}
.hero-title h1{font-size:27px;letter-spacing:.5px;line-height:1.2}
.hero-title p{font-size:23px;margin-top:10px;letter-spacing:.5px}
.btn{display:inline-block;background:var(--red);color:var(--white);font-weight:700;font-size:14px;padding:11px 15px;border-radius:2px}
.hero .btn{position:absolute;left:105px;top:336px}
.dots{position:absolute;left:105px;top:403px;display:flex;gap:8px}
.dots span{width:10px;height:10px;border-radius:50%;background:var(--white)}
.dots span.off{background:transparent;border:2px solid var(--white)}
.hero-wave{position:absolute;left:0;bottom:0;width:1200px;height:140px}

/* intro cards */
.intro-card{position:absolute;top:814px;width:290px;height:338px;border:1px solid var(--line);border-radius:8px;background:var(--white);box-shadow:0 2px 8px rgba(0,0,0,.06);text-align:center;padding:6px}
.intro-card .thumb{height:192px;border-radius:8px}
.intro-card p{font-size:12.5px;line-height:1.7;color:var(--muted);margin-top:20px;padding:0 12px}
.intro-card strong{display:block;font-size:13px;color:var(--ink);margin-top:22px;line-height:1.7}
.intro-card .btn{margin-top:10px;padding:10px 18px}

/* about */
.about{position:absolute;top:1221px;left:0;width:1200px;height:491px;background:linear-gradient(180deg,#4560ad 0%,#3d5aa8 70%,#3a55a0 100%)}
.about-mark{position:absolute;left:160px;top:150px;display:flex;align-items:center;gap:20px;color:var(--white)}
.about-mark .sq{width:40px;height:40px;border:4px solid var(--white)}
.about-mark .name{font-size:110px;font-weight:800;letter-spacing:4px}
.about-copy{position:absolute;left:641px;top:95px;width:450px;color:var(--white)}
.about-copy h2{font-size:29px;font-weight:700}
.about-copy p{font-size:14.5px;line-height:1.65;margin-top:10px}
.btn-outline{display:inline-block;border:1.5px solid var(--white);color:var(--white);font-weight:700;font-size:14px;padding:10px 16px;margin-top:30px}

/* feature tiles */
.tile{position:absolute;top:1833px;width:471px;height:362px;border-radius:4px;overflow:hidden}
.tile .bg{position:absolute;inset:0}
.tile .copy{position:absolute;left:29px;bottom:22px;color:var(--white);width:360px}
.tile h3{font-size:20px;font-weight:700}
.tile p{font-size:12px;line-height:1.55;margin-top:8px}
.tile .link{display:inline-block;font-size:13px;font-weight:700;text-decoration:underline;margin-top:6px}

/* members */
.section-title{position:absolute;left:0;width:1200px;text-align:center;font-size:29px;font-weight:700;color:var(--ink)}
.members-text{position:absolute;left:118px;top:2345px;width:964px;text-align:center;font-size:13px;line-height:1.6;color:var(--muted)}
.members-btn{position:absolute;left:493px;top:2421px}
.dinner-photo{position:absolute;top:2462px;left:0;width:1200px;height:422px;
  background:
    radial-gradient(ellipse 420px 160px at 600px 160px,rgba(255,240,215,.55),rgba(255,240,215,0) 70%),
    linear-gradient(180deg,#f3eee7 0%,#c4a88a 20%,#7d5a3e 50%,#4a3426 78%,#2e2119 100%)}
.dinner-caption{position:absolute;right:28px;bottom:10px;font-size:27px;font-weight:600;color:var(--white);white-space:nowrap}
.mission{position:absolute;top:2884px;left:0;width:1200px;height:324px;background:linear-gradient(180deg,#3f5bab,#3a55a3);color:var(--white);text-align:center}
.mission h2{position:absolute;top:78px;left:140px;width:920px;font-size:28px;line-height:1.45;font-weight:700}
.mission p{position:absolute;top:218px;left:0;width:1200px;font-size:14px}

/* events */
.event{position:absolute;top:3370px;width:288px;height:418px;border:1px solid var(--line);border-radius:8px;background:var(--white);box-shadow:0 2px 8px rgba(0,0,0,.06);padding:7px 10px}
.event .thumb{height:180px;border-radius:10px}
.event .date{display:flex;align-items:center;gap:4px;font-size:13.5px;color:var(--crimson);margin-top:14px}
.event h4{font-size:17px;font-weight:700;color:#333;line-height:1.3;margin-top:8px;padding-left:6px;max-width:250px}
.event h5{font-size:15px;font-weight:700;color:var(--ink);line-height:1.35;margin-top:14px;padding-left:6px}
.event .note{font-size:12.5px;color:var(--muted);line-height:1.45;margin-top:2px;padding-left:6px}
.event .btn{position:absolute;left:17px;top:360px;padding:11px 12px}
.arrow{position:absolute;top:3540px;width:22px;height:22px}

/* footer */
.footer-bg{position:absolute;top:3800px;left:0;width:1200px;height:641px}
.foot-brand{position:absolute;left:105px;top:4030px;display:flex;align-items:center;gap:10px}
.foot-brand .dot{width:16px;height:16px;border-radius:50%;background:var(--crimson)}
.foot-brand .name{font-size:40px;font-weight:800;color:var(--navy);letter-spacing:1px}
.foot-col{position:absolute;top:4017px;color:var(--white)}
.foot-col h6{font-size:18px;font-weight:600}
.foot-col h6::after{content:"";display:block;width:48px;height:3px;background:var(--white);margin-top:10px}
.quick ul{margin-top:2px}
.quick li{list-style:none;font-size:14px;margin-top:17px}
.contact-row{display:flex;align-items:center;gap:8px;font-weight:700;font-size:15px;margin-top:18px}
.contact-row .ico{width:26px;height:26px;border-radius:50%;background:var(--crimson);display:flex;align-items:center;justify-content:center}
.contact-val{font-size:13px;line-height:1.5;margin-top:8px}
.news p{font-size:12px;line-height:1.8;margin-top:16px;width:250px}
.news .field{width:250px;height:34px;background:var(--white);color:#333;font-size:12px;display:flex;align-items:center;gap:6px;padding:0 10px;margin-top:12px;border:1px solid #ccc}
.news .sub{width:250px;height:34px;background:var(--crimson);color:var(--white);font-size:12px;font-weight:700;display:flex;align-items:center;justify-content:center;margin-top:8px}
.copyright{position:absolute;top:4377px;left:0;width:1200px;text-align:center;color:var(--white);font-size:11.5px}
</style>
</head>
<body>

<header class="site-header">
  <div class="brand"><span class="brand-dot"></span><span class="brand-name">FSEA</span></div>
  <div class="brand-sub">BRITISH SECTION</div>
  <nav class="main-nav">
    <a>About Us</a><a>News &amp; Programme</a><a>Gallery</a><a>Downloads</a><a>Contact Us</a><a>Members Section</a>
  </nav>
</header>

<section class="hero">
  <div class="hero-photo" role="img" aria-label="Engineer in hard hat and high-visibility vest overlooking a construction site at sunset"></div>
  <div class="hero-shade"></div>
  <div class="hero-brand"><span class="mark"></span><span class="name">FSEA</span></div>
  <div class="hero-tag">Société des Savants et Ingénieurs Associés</div>
  <div class="hero-title">
    <h1>Welcome to the British Section of the FSEA</h1>
    <p>Sharing knowledge and a love of France</p>
  </div>
  <a class="btn">Get Started</a>
  <div class="dots"><span></span><span class="off"></span><span></span></div>
  <svg class="hero-wave" viewBox="0 0 1200 140" preserveAspectRatio="none">
    <path d="M0 40 C250 140 520 130 780 80 C960 45 1100 20 1200 0 L1200 140 L0 140Z" fill="#c8003f"/>
    <path d="M0 62 C250 150 520 145 780 100 C960 68 1100 45 1200 30 L1200 140 L0 140Z" fill="#ffffff"/>
  </svg>
</section>

<div class="intro-card" style="left:133px">
  <div class="thumb" role="img" aria-label="Engineers in safety gear on a construction site" style="background:linear-gradient(180deg,#d9cdb8 0%,#b59c78 45%,#8b7657 75%,#5c5140 100%)"></div>
  <p>An informal society of engineers and scientists, giving equal importance to the quality of our technical activities and our fellowship.</p>
</div>
<div class="intro-card" style="left:459px">
  <div class="thumb" role="img" aria-label="Scientist working at a microscope in a laboratory" style="background:radial-gradient(ellipse 120px 90px at 200px 70px,rgba(220,235,245,.8),rgba(220,235,245,0) 70%),linear-gradient(160deg,#1c3d5c,#2e7aa8 55%,#8fc0dc)"></div>
  <p>We provide high quality lectures and technical visits on diverse engineering and scientific subjects, and the enjoyment of Frenchculture and Cuisine.</p>
</div>
<div class="intro-card" style="left:784px">
  <div class="thumb" role="img" aria-label="Two scientists examining samples in a bright laboratory" style="background:linear-gradient(160deg,#f4f6f9,#d4dde6 55%,#a9b8c8)"></div>
  <strong>New members are always<br>welcome</strong>
  <a class="btn">Learn More</a>
</div>

<section class="about">
  <div class="about-mark"><span class="sq"></span><span class="name">FSEA</span></div>
  <div class="about-copy">
    <h2>ABOUT US</h2>
    <p>We are an informal society of engineers and scientists. A very friendly organisation where equal importance is given to the quality of our technical activities and our fellowship, where our partners are involved and welcomed in everything we do.</p>
    <a class="btn-outline">Read More</a>
  </div>
</section>

<div class="tile" style="left:121px">
  <div class="bg" role="img" aria-label="Engineers in hard hats walking through a building under construction" style="background:linear-gradient(180deg,#b98aa2 0%,#d2508a 55%,#c2144f 100%)"></div>
  <div class="copy">
    <h3>Our Activities</h3>
    <p>Five or six high quality technical lectures are arranged throughout the year at a number of London venues followed by dinner.</p>
    <a class="link">Read Activities</a>
  </div>
</div>
<div class="tile" style="left:609px">
  <div class="bg" role="img" aria-label="Suspension bridge and arch bridge crossing a river under a grey sky" style="background:linear-gradient(180deg,#5f6266 0%,#9a9ea3 40%,#7b8078 62%,#4f5650 100%)"></div>
  <div class="copy">
    <h3>Our History</h3>
    <a class="link">Read Activities</a>
  </div>
</div>

<h2 class="section-title" style="top:2290px">OUR MEMBERS</h2>
<p class="members-text">The origins of the Section lie in civil engineering. For many years, however, in line with the now named Société des Savants et Ingénieurs Associés (FSEA), we have been open to membership from like minded people from all fields of engineering and science. We are always delighted to welcome new members. If you would like to join us or would like further information on membership,</p>
<a class="btn members-btn">Please Click Membership</a>

<div class="dinner-photo" role="img" aria-label="Members seated at round tables during a formal society dinner in a grand hall">
  <span class="dinner-caption">Celebrating our Centenary</span>
</div>

<section class="mission">
  <h2>The Society For Engineers And Scientists Where They Sample French Cuisine And Culture With Their Partners As Well As Continue Their Professional Interests</h2>
  <p>And Annual General MeetingAt the Hall of Applied Engineering, 12 Meridian Row</p>
</section>

<h2 class="section-title" style="top:3294px">UPCOMING EVENTS</h2>

<svg class="arrow" style="left:46px" viewBox="0 0 22 22"><circle cx="11" cy="11" r="11" fill="#395394"/><path d="M13 6 L8 11 L13 16" stroke="#fff" stroke-width="2.5" fill="none"/><path d="M8 11 H16" stroke="#fff" stroke-width="2.5"/></svg>
<svg class="arrow" style="left:1132px" viewBox="0 0 22 22"><circle cx="11" cy="11" r="11" fill="#9a9a9a"/><path d="M9 6 L14 11 L9 16" stroke="#fff" stroke-width="2.5" fill="none"/><path d="M6 11 H14" stroke="#fff" stroke-width="2.5"/></svg>

<div class="event" style="left:143px">
  <div class="thumb" role="img" aria-label="Fire investigator inspecting burnt debris" style="background:linear-gradient(160deg,#5a5a56,#2a2a28 50%,#8a8a6a)"></div>
  <div class="date"><svg width="13" height="13" viewBox="0 0 13 13"><rect x="1" y="2" width="11" height="10" rx="1" fill="none" stroke="#e00053" stroke-width="1.5"/><path d="M1 5 H12" stroke="#e00053" stroke-width="1.5"/></svg>Monday 29 January 2024</div>
  <h4>Incoming President's Inaugural lecture and dinner</h4>
  <h5>Forensic Fire Investigation :</h5>
  <p class="note">The Underpinning Fire Science And Investigative Methodology</p>
  <a class="btn">Learn More</a>
</div>
<div class="event" style="left:457px">
  <div class="thumb" role="img" aria-label="Forest wildfire with flames among tree trunks" style="background:linear-gradient(180deg,#5a1a0a,#c2410c 50%,#f59e0b)"></div>
  <div class="date"><svg width="13" height="13" viewBox="0 0 13 13"><rect x="1" y="2" width="11" height="10" rx="1" fill="none" stroke="#e00053" stroke-width="1.5"/><path d="M1 5 H12" stroke="#e00053" stroke-width="1.5"/></svg>Tuesday 19 March 2024</div>
  <h4>Evening Lecture and<br>Dinner</h4>
  <h5>How To Protect People And Homes From Wildfires :</h5>
  <a class="btn">Learn More</a>
</div>
<div class="event" style="left:769px">
  <div class="thumb" role="img" aria-label="Smoke rising from a tower block above a city" style="background:linear-gradient(180deg,#c9d3dc,#8d96a0 50%,#4c5a4c)"></div>
  <div class="date"><svg width="13" height="13" viewBox="0 0 13 13"><rect x="1" y="2" width="11" height="10" rx="1" fill="none" stroke="#e00053" stroke-width="1.5"/><path d="M1 5 H12" stroke="#e00053" stroke-width="1.5"/></svg>Tuesday 30 April 2024</div>
  <h4>Evening Lecture and<br>Dinner</h4>
  <h5>Unplanned Adventures In Fire Science, Engineering, And Regulation</h5>
  <a class="btn">Learn More</a>
</div>

<svg class="footer-bg" viewBox="0 0 1200 641" preserveAspectRatio="none">
  <path d="M0 30 C250 90 520 120 800 90 C980 70 1100 40 1200 10 L1200 641 L0 641Z" fill="#c8003f"/>
  <path d="M0 70 C250 130 520 150 800 125 C980 108 1100 80 1200 55 L1200 641 L0 641Z" fill="#000000"/>
</svg>

<div class="foot-brand"><span class="dot"></span><span class="name">FSEA</span></div>

<div class="foot-col quick" style="left:352px">
  <h6>Quick Links</h6>
  <ul><li>About Us</li><li>News &amp; Programme</li><li>Gallery</li><li>Downloads</li><li>Contact Us</li><li>Members Section</li></ul>
</div>

<div class="foot-col" style="left:552px;width:280px">
  <h6>Contact Details</h6>
  <div class="contact-row"><span class="ico"><svg width="12" height="14" viewBox="0 0 12 14"><path d="M6 0 C2.7 0 0 2.6 0 5.8 C0 9.8 6 14 6 14 C6 14 12 9.8 12 5.8 C12 2.6 9.3 0 6 0Z" fill="#fff"/><circle cx="6" cy="5.8" r="2" fill="#e00053"/></svg></span>Address :</div>
  <p class="contact-val">FSEA British Section Secretariat<br>c/o Clara Whitmore, Hall of Applied<br>Engineering, 12 Meridian Row<br>Southbank, London, SE1 9ZQ</p>
  <div class="contact-row"><span class="ico"><svg width="12" height="12" viewBox="0 0 12 12"><path d="M2.5 0.5 L4.5 3 L3.3 4.4 C4 6 5.9 7.9 7.6 8.7 L9 7.5 L11.5 9.5 L10.2 11.5 C5.5 11.2 0.8 6.5 0.5 1.8Z" fill="#fff"/></svg></span>Telephone :</div>
  <p class="contact-val">020 7946 0321</p>
  <div class="contact-row"><span class="ico"><svg width="12" height="10" viewBox="0 0 12 10"><rect x="0" y="0" width="12" height="10" rx="1" fill="#fff"/><path d="M0.5 1 L6 5.5 L11.5 1" stroke="#e00053" stroke-width="1.3" fill="none"/></svg></span>E - mail :</div>
  <p class="contact-val">clara.whitmore@fsea-section.org</p>
</div>

<div class="foot-col news" style="left:846px">
  <h6>Newsletter</h6>
  <p>Lorem ipsum dolor sit amet, consectetur adipiscing elit, sed do</p>
  <div class="field"><svg width="11" height="9" viewBox="0 0 12 10"><rect x="0" y="0" width="12" height="10" rx="1" fill="#333"/><path d="M0.5 1 L6 5.5 L11.5 1" stroke="#fff" stroke-width="1.3" fill="none"/></svg>Enter Email</div>
  <div class="sub">SUBSCRIBE</div>
</div>

<p class="copyright">©Copyrights 2023 FSEA | All Rights Reserved</p>

</body>
</html>
```